Construction company business card

One side to be the logo with the company name, The other side I would like: (Tomas verbick) Project manager 41 barrow crescent hallam 52917306224783(03) 9703 2428Info@gudeljgroup.comAnd then maybe a couple dot points saying what we do:Construction (commercial & industrial) Civil construction

Anything else please contact me!
Maybe curved st one edge of the card

Target Market(s)

Older clientele

Industry/Entity Type

Construction Company

Contact Information for Business Card

Read above

Colors
3277b5
1b1b1b
9d9d9d

Requirements
Must have
• Use my logo on one side
Nice to have
• Read above
Should not have
• Read above

```html
<!DOCTYPE html>
<html lang="en">
<head>
<meta charset="utf-8">
<title>Stonefield Property Group – Business Card</title>
<link href="https://fonts.googleapis.com/css2?family=Lato:wght@400;700;900&display=swap" rel="stylesheet">
<style>
  :root {
    --brand-blue: #3277b5;
    --ink: #1b1b1b;
    --steel: #9d9d9d;
    --paper: #f6f6f6;
    --backdrop: #e4e4e4;
    --white: #ffffff;
    --rule: rgba(255, 255, 255, 0.45);
  }
  * { box-sizing: border-box; margin: 0; padding: 0; }
  html, body {
    width: 1200px;
    height: 900px;
    overflow: hidden;
    background: var(--backdrop);
    font-family: "Lato", Arial, sans-serif;
  }
  .business-card {
    position: absolute;
    left: 120px;
    top: 153px;
    width: 960px;
    height: 594px;
    background: var(--paper);
    box-shadow: 0 10px 30px rgba(0, 0, 0, 0.15);
    overflow: hidden;
  }
  .brand-side {
    position: absolute;
    left: 0; top: 0;
    width: 498px; height: 100%;
  }
  .brand-mark {
    position: absolute;
    left: 152px;
    top: 150px;
    width: 172px;
    height: 172px;
    border-radius: 50%;
    background: var(--brand-blue);
  }
  .brand-name {
    position: absolute;
    left: 0;
    width: 476px;
    text-align: center;
    color: var(--brand-blue);
    font-weight: 900;
    line-height: 1;
  }
  .brand-name--main { top: 364px; font-size: 52px; letter-spacing: 1px; }
  .brand-name--sub { top: 414px; font-size: 20px; letter-spacing: 7px; }
  .edge-stripe {
    position: absolute;
    left: 498px; top: 0;
    width: 6px; height: 100%;
    background: var(--steel);
  }
  .contact-side {
    position: absolute;
    left: 504px; top: 0;
    width: 456px; height: 100%;
    background: var(--brand-blue);
    color: var(--white);
  }
  .badge-dot {
    position: absolute;
    left: -33px;
    top: 58px;
    width: 60px;
    height: 60px;
    border-radius: 50%;
    background: var(--white);
  }
  .person-name {
    position: absolute;
    left: 63px; top: 58px;
    font-size: 36px;
    font-weight: 700;
    letter-spacing: 0.5px;
  }
  .person-role {
    position: absolute;
    left: 63px; top: 97px;
    font-size: 25px;
  }
  .contact-line {
    position: absolute;
    left: 63px;
    display: flex;
    align-items: center;
    gap: 8px;
    font-size: 25px;
    line-height: 1.38;
  }
  .contact-line svg { width: 20px; height: 20px; flex: none; fill: var(--white); }
  .contact-line--phone { top: 172px; }
  .contact-line--mobile { top: 207px; }
  .contact-line--email { top: 242px; }
  .contact-line--address { top: 292px; align-items: flex-start; }
  .contact-line--address svg { margin-top: 8px; }
  .divider {
    position: absolute;
    left: 59px; top: 418px;
    width: 346px; height: 1px;
    background: var(--rule);
  }
  .services {
    position: absolute;
    left: 58px; top: 438px;
    list-style: none;
    font-size: 25px;
    line-height: 1.38;
  }
  .services li { position: relative; padding-left: 20px; }
  .services li::before {
    content: "";
    position: absolute;
    left: 0; top: 11px;
    width: 14px; height: 14px;
    border-radius: 50%;
    background: var(--white);
  }
</style>
</head>
<body>
  <div class="business-card">
    <section class="brand-side">
      <div class="brand-mark"></div>
      <div class="brand-name brand-name--main">STONEFIELD</div>
      <div class="brand-name brand-name--sub">PROPERTY GROUP</div>
    </section>
    <div class="edge-stripe"></div>
    <section class="contact-side">
      <div class="badge-dot"></div>
      <h1 class="person-name">TOMAS VERBICK</h1>
      <p class="person-role">Project manager</p>

      <p class="contact-line contact-line--phone">
        <svg viewBox="0 0 24 24" aria-hidden="true"><path d="M2 9c0-3 5-5 10-5s10 2 10 5v2h-5V9c-1-1-3-1.5-5-1.5S8 8 7 9v2H2z"/><path d="M6 12h12l2 8H4z"/></svg>
        7306224783
      </p>
      <p class="contact-line contact-line--mobile">
        <svg viewBox="0 0 24 24" aria-hidden="true"><path d="M7 1h10a2 2 0 0 1 2 2v18a2 2 0 0 1-2 2H7a2 2 0 0 1-2-2V3a2 2 0 0 1 2-2zm0 3v14h10V4zm5 15.5a1.2 1.2 0 1 0 0 2.4 1.2 1.2 0 0 0 0-2.4z"/></svg>
        (03) 9418 6573
      </p>
      <p class="contact-line contact-line--email">
        <svg viewBox="0 0 24 24" aria-hidden="true"><path d="M2 5h20v14H2zm2 2v.5l8 5.5 8-5.5V7l-8 5.5z"/></svg>
        Info@verbickgroup.com
      </p>
      <p class="contact-line contact-line--address">
        <svg viewBox="0 0 24 24" aria-hidden="true"><path d="M12 1a8 8 0 0 0-8 8c0 6 8 14 8 14s8-8 8-14a8 8 0 0 0-8-8zm0 11a3 3 0 1 1 0-6 3 3 0 0 1 0 6z"/></svg>
        <span>41 barrow crescent<br>kellbrook 5291</span>
      </p>

      <div class="divider"></div>

      <ul class="services">
        <li>Construction<br>(commercial &amp; industrial)</li>
        <li>Civil construction</li>
      </ul>
    </section>
  </div>
</body>
</html>
```